Etiketten für Bio Seifen
Zielgruppe
Wir stellen hochwertig 'handgemachte' Bio-Seifen her. Die Zielgruppe ist von 3-99 Jahren und zusätzlich haben wir auch noch Seife für Hunde.
Der Firmenname ist 'Verdolina'
Aufgabenstellung
Das Etikett soll Bezug auf Natur, Bio, Nachhaltigkeit nehmen. Wir stellen uns 'weiche' Aquarellfarben vor...Seife: Lavendel, Calendular, 7 Kräuter etc.
Das Etikett soll auf eine Beutelschachtel. Die Schachtel hat eine Anmaße: Breite 55mm; Höhe 120mm; Tiefe 30mm
Das Etikett soll im vorderen- und hinteren Bereich zusammenhängend geklebt werden.
Das Etikett soll eine Abmaße von: Breite 51mm; Höhe 114mm haben (Vorderseite) Rückseite gleich.
Wir möchten die Produkte auch gerne nummerieren, d.h. jede Seife hat eine Nummer die nicht zu groß dargestellt werden soll aber trotzdem gut leserlich.
Wir haben noch ein paar Bilder hochgeladen wie wir uns das ungefähr vorstellen.

```html
<!DOCTYPE html>
<html lang="de">
<head>
<meta charset="utf-8">
<title>Bio Seife – Etikett Vorderseite</title>
<link rel="stylesheet" href="https://fonts.googleapis.com/css2?family=Dancing+Script:wght@600;700&family=Amatic+SC:wght@400;700&display=swap">
<style>
  :root {
    --stage: #e9e9ec;
    --lavender-pale: #f3eff8;
    --lavender-soft: #dcd0ec;
    --lavender-mid: #c5b4e0;
    --lavender-deep: #9a8bb4;
    --ink-deep: #3f2a78;
    --ink-light: #9c86cf;
    --ribbon: #b9a6dc;
    --ribbon-text: #4a3684;
    --art-light: #e4dcef;
    --art-dark: #cbbde2;
  }
  html, body {
    margin: 0;
    width: 1098px;
    height: 1200px;
    overflow: hidden;
    background: var(--stage);
  }
  .label {
    position: absolute;
    left: 303px;
    top: 50px;
    width: 492px;
    height: 1100px;
    overflow: hidden;
    background:
      radial-gradient(ellipse 70% 30% at 75% 20%, var(--lavender-mid) 0%, transparent 70%),
      radial-gradient(ellipse 60% 25% at 20% 55%, rgba(255,255,255,0.8) 0%, transparent 70%),
      radial-gradient(ellipse 80% 35% at 70% 85%, var(--lavender-deep) 0%, transparent 75%),
      radial-gradient(ellipse 60% 30% at 15% 90%, rgba(255,255,255,0.9) 0%, transparent 70%),
      linear-gradient(180deg, var(--lavender-pale) 0%, var(--lavender-soft) 45%, var(--lavender-mid) 100%);
  }
  .title {
    position: absolute;
    left: 0;
    right: 0;
    top: 250px;
    margin: 0;
    text-align: center;
    font-family: "Dancing Script", cursive;
    line-height: 1;
  }
  .title-bio {
    display: block;
    font-size: 130px;
    font-weight: 700;
    color: var(--ink-deep);
    margin-left: 40px;
  }
  .title-seife {
    display: block;
    font-size: 215px;
    font-weight: 600;
    color: var(--ink-light);
    margin-top: -70px;
  }
  .wreath-art {
    position: absolute;
    left: 46px;
    top: 570px;
    width: 400px;
    height: 400px;
    border-radius: 50%;
    background: radial-gradient(circle at 50% 50%, var(--art-light) 0%, var(--art-dark) 100%);
  }
  .ribbon {
    position: absolute;
    left: 90px;
    top: 990px;
    width: 320px;
    height: 80px;
  }
  .ribbon-text {
    font-family: "Amatic SC", sans-serif;
    font-size: 46px;
    font-weight: 400;
    fill: var(--ribbon-text);
    letter-spacing: 2px;
  }
</style>
</head>
<body>
  <main class="label">
    <div class="wreath-art" role="img" aria-label="Aquarell-Kranz aus Lavendel, Ringelblumen und Kräutern um ein gezeichnetes Seifenstück mit der Aufschrift Handgemacht"></div>
    <h1 class="title">
      <span class="title-bio">Bio</span>
      <span class="title-seife">Seife</span>
    </h1>
    <svg class="ribbon" viewBox="0 0 320 80">
      <path d="M4 8 L316 14 L300 42 L316 74 L10 66 L22 38 Z" fill="var(--ribbon)" opacity="0.85"/>
      <text class="ribbon-text" x="160" y="54" text-anchor="middle">MIT KRÄUTERN</text>
    </svg>
  </main>
</body>
</html>
```